Business IT Services Billboard to attract local small businesses

We are Brivoqua, a premier Managed Service Provider (MSP) specializing in comprehensive IT services and VOIP phone solutions exclusively for businesses. Our goal is to create a dynamic and visually engaging billboard advertisement that not only highlights our cutting-edge IT solutions but also emphasizes our state-of-the-art VOIP phone services. This billboard should communicate our commitment to providing innovative, reliable, and holistic technology solutions.
See the attached supporting documentation.
Target Market(s)
small business
Industry/Entity Type
Information Technology
Colors
Designer to choose colors to be used in the design.
Look and feel
Each slider illustrates characteristics of the customer's brand and the style your logo design should communicate.

```html
<!DOCTYPE html>
<html lang="en">
<head>
<meta charset="utf-8">
<title>Brivoqua Billboard</title>
<link rel="stylesheet" href="https://fonts.googleapis.com/css2?family=Montserrat:wght@500;600;800;900&display=swap">
<style>
  :root {
    --brand-blue: #0b6dbb;
    --brand-navy: #163a66;
    --ink-navy: #17325a;
    --accent-gray: #b3b3b3;
    --paper: #ffffff;
    --stage: #eceff3;
    --photo-dark: #5c6470;
    --photo-light: #b9aa92;
  }
  * { margin: 0; padding: 0; box-sizing: border-box; }
  html, body {
    width: 1189px;
    height: 1200px;
    overflow: hidden;
    background: var(--stage);
    font-family: "Montserrat", Arial, sans-serif;
  }
  .billboard {
    position: absolute;
    left: 0;
    top: 427px;
    width: 1189px;
    height: 345px;
    background: var(--paper);
    overflow: hidden;
  }
  .billboard-shapes {
    position: absolute;
    inset: 0;
    width: 100%;
    height: 100%;
  }
  .brand-name {
    position: absolute;
    left: 38px;
    top: 14px;
    font-size: 70px;
    font-weight: 900;
    letter-spacing: 5px;
    line-height: 1;
    color: var(--brand-blue);
  }
  .headline {
    position: absolute;
    left: 38px;
    top: 100px;
    font-size: 40px;
    font-weight: 800;
    line-height: 41px;
    color: var(--paper);
    text-transform: uppercase;
    letter-spacing: 0.2px;
  }
  .tagline {
    position: absolute;
    left: 38px;
    top: 230px;
    padding-left: 9px;
    border-left: 2px solid var(--paper);
    font-size: 16.5px;
    font-weight: 500;
    line-height: 19px;
    color: var(--paper);
    letter-spacing: 0.3px;
  }
  .web-cta {
    position: absolute;
    left: 37px;
    top: 282px;
    width: 297px;
    height: 55px;
    background: var(--brand-navy);
    color: var(--paper);
    padding: 5px 0 0 9px;
  }
  .web-cta-lead {
    font-size: 12.5px;
    font-weight: 500;
    line-height: 15px;
    letter-spacing: 0.2px;
  }
  .web-cta-url {
    font-size: 24px;
    font-weight: 600;
    line-height: 28px;
    letter-spacing: 0.3px;
  }
  .phone-cta {
    position: absolute;
    left: 348px;
    top: 295px;
    display: flex;
    align-items: center;
    gap: 5px;
    color: var(--ink-navy);
    font-size: 27px;
    font-weight: 800;
    line-height: 1;
  }
  .phone-icon { width: 30px; height: 30px; }
</style>
</head>
<body>
  <div class="billboard">
    <svg class="billboard-shapes" viewBox="0 0 1762 512" preserveAspectRatio="none" aria-hidden="false">
      <defs>
        <linearGradient id="officePhotoTone" x1="0" y1="0" x2="1" y2="1">
          <stop offset="0" stop-color="var(--photo-dark)"/>
          <stop offset="0.55" stop-color="#8a8d93"/>
          <stop offset="1" stop-color="var(--photo-light)"/>
        </linearGradient>
      </defs>
      <polygon class="office-photo" role="img" aria-label="Photo: three business colleagues gathered around a laptop at an office desk"
               points="1120,0 1762,0 1762,512 1068,512 988,330" fill="url(#officePhotoTone)"/>
      <polygon class="headline-panel" points="0,127 1032,127 952,430 0,430" fill="var(--brand-blue)"/>
      <polygon class="accent-stripe" points="1094,0 1118,0 966,408 944,408" fill="var(--brand-blue)"/>
      <polygon class="accent-triangle" points="985,333 1068,512 925,512" fill="var(--accent-gray)"/>
    </svg>

    <div class="brand-name">BRIVOQUA</div>

    <h1 class="headline">Elevate your business<br>with next-gen IT and<br>VOIP services</h1>

    <p class="tagline">Innovative IT and VOIP Solutions Tailored<br>for Your Business Success.</p>

    <div class="web-cta">
      <div class="web-cta-lead">Transform Your Tech Today at</div>
      <div class="web-cta-url">www.brivoqua.com</div>
    </div>

    <div class="phone-cta">
      <svg class="phone-icon" viewBox="0 0 30 30" aria-hidden="true">
        <circle cx="15" cy="15" r="13.5" fill="none" stroke="var(--brand-blue)" stroke-width="2"/>
        <path d="M10.2 8.3c.6-.5 1.4-.4 1.8.2l1.4 2.2c.3.5.2 1.2-.2 1.6l-.9.8c.6 1.6 1.8 3 3.4 3.8l.9-.8c.4-.4 1.1-.5 1.6-.1l2.1 1.5c.6.4.7 1.3.2 1.8l-1 1.1c-.8.8-2 1-3.1.6-3.9-1.5-6.6-4.6-7.7-8.5-.3-1 0-2.1.8-2.8z" fill="var(--brand-blue)"/>
        <path d="M16.5 9.2a5 5 0 0 1 4.3 4.3M16.8 6.5a7.6 7.6 0 0 1 6.7 6.7" fill="none" stroke="var(--brand-blue)" stroke-width="1.4" stroke-linecap="round"/>
      </svg>
      <span class="phone-number">(555) 013-4872</span>
    </div>
  </div>
</body>
</html>
```